We need letterhead, Business Cards, and envelops designed. We have attached a design of our logo and a sample of letterhead idea that was started but never perfected, it is only an idea for the letterhead if you can design something better we may love that also we are open to change.
We want a design that looks professional in style. we are a non profit trade association in the construction industry. the green color in the attached design represent green building, and we like that. also if you just want to enhance the letterhead sample that we attached that would be fine also.
Thanks and good luck
also the name that should show on the first business cards should be Morgan Feltwick, Director are web address is www.pvtrn.org

```html
<!DOCTYPE html>
<html lang="en">
<head>
<meta charset="utf-8">
<title>PVTRN Business Card – Morgan Feltwick</title>
<link rel="stylesheet" href="https://fonts.googleapis.com/css2?family=Cinzel:wght@600&family=Didact+Gothic&display=swap">
<style>
  :root {
    --paper: #ffffff;
    --ink: #000000;
    --leaf: #3f7d1e;
    --leaf-light: #8fd45a;
    --text-light: #ffffff;
  }
  * { margin: 0; padding: 0; box-sizing: border-box; }
  html, body { width: 1200px; height: 667px; overflow: hidden; background: var(--paper); }
  .card {
    position: relative;
    width: 1200px;
    height: 667px;
    background: var(--paper);
    font-family: "Didact Gothic", "Century Gothic", sans-serif;
  }
  .brand {
    position: absolute;
    left: 0; right: 0;
    top: 92px;
    display: flex;
    justify-content: center;
    align-items: center;
    gap: 22px;
  }
  .brand__mark {
    width: 34px; height: 34px;
    background: var(--leaf);
  }
  .brand__name {
    font-family: "Didact Gothic", "Century Gothic", sans-serif;
    font-size: 138px;
    line-height: 1;
    letter-spacing: 4px;
    color: var(--ink);
  }
  .info-band {
    position: absolute;
    left: 0; top: 298px;
    width: 1200px; height: 307px;
    background: var(--ink);
    color: var(--text-light);
  }
  .person {
    position: absolute;
    left: 175px; top: 40px;
  }
  .person__name {
    font-family: "Cinzel", Georgia, serif;
    font-weight: 600;
    font-size: 30px;
    letter-spacing: 3px;
    line-height: 1.2;
  }
  .person__role {
    margin-top: 2px;
    font-size: 26px;
    letter-spacing: 2.5px;
    color: var(--leaf);
  }
  .contact {
    position: absolute;
    left: 656px; top: 38px;
    font-size: 24px;
    letter-spacing: 3px;
    line-height: 35px;
  }
  .contact__list {
    list-style: none;
    margin-top: 23px;
  }
  .contact__item {
    display: flex;
    align-items: center;
  }
  .contact__icon {
    width: 22px; height: 22px;
    margin-left: 2px;
    margin-right: 45px;
    fill: var(--leaf);
    stroke: var(--leaf);
  }
</style>
</head>
<body>
<main class="card">
  <header class="brand">
    <span class="brand__name">PVTRN</span>
    <span class="brand__mark" aria-hidden="true"></span>
  </header>

  <section class="info-band">
    <div class="person">
      <h1 class="person__name">Morgan Feltwick</h1>
      <p class="person__role">Director</p>
    </div>

    <address class="contact" style="font-style:normal">
      <p>address</p>
      <p>4321 first street</p>
      <p>anytown, State ZIP</p>
      <ul class="contact__list">
        <li class="contact__item">
          <svg class="contact__icon" viewBox="0 0 24 24" aria-label="Phone">
            <path d="M3 9c0-3 4-5 9-5s9 2 9 5v1h-5V8c-1-.6-2.5-1-4-1s-3 .4-4 1v2H3z" stroke="none"/>
            <rect x="6" y="11" width="12" height="9" rx="2" fill="none" stroke-width="2"/>
            <circle cx="12" cy="15.5" r="2" stroke="none"/>
          </svg>
          <span>123-456-7890</span>
        </li>
        <li class="contact__item">
          <svg class="contact__icon" viewBox="0 0 24 24" aria-label="Fax">
            <rect x="7" y="3" width="10" height="6" fill="none" stroke-width="2"/>
            <rect x="3" y="9" width="18" height="8" rx="1.5" stroke="none"/>
            <rect x="7" y="14" width="10" height="7" fill="var(--ink)" stroke-width="2"/>
          </svg>
          <span>123-456-7891</span>
        </li>
        <li class="contact__item">
          <svg class="contact__icon" viewBox="0 0 24 24" aria-label="Website">
            <g fill="none" stroke-width="1.8">
              <circle cx="11" cy="11" r="8"/>
              <ellipse cx="11" cy="11" rx="3.5" ry="8"/>
              <path d="M3 11h16M5 6.5h12M5 15.5h12"/>
            </g>
            <path d="M14 14l8 3-3.5 1.2L17 22z" stroke="none"/>
          </svg>
          <span>www.pvtrn.org</span>
        </li>
      </ul>
    </address>
  </section>
</main>
</body>
</html>
```